Foot doctor needs feet friendly business cards.

Business cards for Podiatrist. Needs to look professional and modern. Back side put an appointment card, and try to put a little basic street map somewhere on card along with all of our contact info below:

Marcus Dovan, DPM, Inc.
Diplomate, National Council of Lower Limb Medicine
Call: 1.877.Toes.482
1.555.283.9146
Fax: 1.555.671.3820
Email: info@DrDovanclinic.example
Web: www.DrDovanclinic.example
2847 W. Harbor Ln. Suite 204
Harborvale, WA 90000

```html
<!DOCTYPE html>
<html lang="en">
<head>
<meta charset="utf-8">
<title>Marcus Dovan, DPM, Inc. – Business Card</title>
<link rel="stylesheet" href="https://fonts.googleapis.com/css2?family=Open+Sans:wght@400;600&display=swap">
<style>
  :root {
    --backdrop: #3b3633;
    --card: #ffffff;
    --card-warm: #fdfbf8;
    --brand-blue: #2b5f94;
    --ink: #2a2a2a;
    --rule: #8fa6bf;
    --skin-light: #f6d9cc;
    --skin-mid: #eab9a6;
  }
  * { box-sizing: border-box; margin: 0; padding: 0; }
  html, body { width: 1200px; height: 844px; overflow: hidden; }
  body {
    background: var(--backdrop);
    font-family: "Open Sans", Arial, sans-serif;
    position: relative;
  }
  .card {
    position: absolute;
    top: 267px;
    width: 540px;
    height: 310px;
    background: var(--card);
    box-shadow: 0 6px 18px rgba(0,0,0,.35);
    overflow: hidden;
  }
  /* ---------- front ---------- */
  .card--front { left: 40px; background: var(--card-warm); }
  .front__photo {
    position: absolute;
    top: 0; right: 0;
    width: 340px; height: 240px;
    background: radial-gradient(ellipse at 55% 40%, var(--skin-mid) 0%, var(--skin-light) 40%, rgba(253,251,248,0) 72%);
  }
  .front__info { position: absolute; left: 38px; top: 92px; color: var(--ink); }
  .front__name { color: var(--brand-blue); font-weight: 600; font-size: 21px; line-height: 1.2; }
  .front__title { font-size: 13.5px; line-height: 17px; margin-top: 4px; }
  .front__address { font-size: 13.5px; line-height: 17px; margin-top: 14px; }
  .contact-list { list-style: none; margin-top: 12px; font-size: 13.5px; line-height: 17px; }
  .contact-list li { display: flex; align-items: center; gap: 7px; }
  .contact-list .icon { width: 12px; height: 12px; flex: none; fill: var(--brand-blue); }
  .contact-list .icon--blank { visibility: hidden; }
  /* ---------- back ---------- */
  .card--back { left: 620px; }
  .appointment__heading {
    text-align: center; color: var(--brand-blue); font-weight: 600;
    font-size: 14px; letter-spacing: .5px; margin-top: 40px;
  }
  .appointment__fields { margin: 22px 40px 0; color: var(--brand-blue); font-size: 13px; }
  .field-row { display: flex; align-items: flex-end; gap: 6px; height: 30px; }
  .field-row .label { white-space: nowrap; }
  .field-row .line { flex: 1; border-bottom: 1px solid var(--rule); height: 14px; }
  .appointment__divider { margin: 22px 40px 0; border: 0; border-top: 1px solid var(--brand-blue); }
  .appointment__note {
    text-align: center; color: var(--brand-blue); font-size: 12.5px;
    line-height: 19px; margin: 14px auto 0; width: 330px;
  }
</style>
</head>
<body>

<section class="card card--front" aria-label="Business card front">
  <div class="front__photo" role="img" aria-label="Photo of a baby's feet held in an adult's hands forming a heart"></div>
  <div class="front__info">
    <h1 class="front__name">Marcus Dovan, DPM, Inc.</h1>
    <p class="front__title">Diplomate, National Council<br>of Lower Limb Medicine</p>
    <p class="front__address">2847 W. Harbor Ln. Suite 204<br>Harborvale, WA 90000</p>
    <ul class="contact-list">
      <li><svg class="icon" viewBox="0 0 12 12"><path d="M1 4c0-2 2-3 5-3s5 1 5 3v1H8V4H4v1H1zM2 6h8l1 5H1z"/></svg>1.877.Toes.482</li>
      <li><svg class="icon icon--blank" viewBox="0 0 12 12"></svg>1.555.283.9146</li>
      <li><svg class="icon" viewBox="0 0 12 12"><path d="M3 1h5l1 1v3h2v6H1V5h2zM4 2v3h4V2zM3 7h2v1H3zm4 0h2v1H7zM3 9h2v1H3zm4 0h2v1H7z"/></svg>1.555.671.3820</li>
      <li><svg class="icon" viewBox="0 0 12 12"><path d="M1 3h10v7H1zM1.8 3.6 6 7l4.2-3.4v1.2L6 8.2 1.8 4.8z" fill-rule="evenodd"/></svg>info@DrDovanclinic.example</li>
      <li><svg class="icon" viewBox="0 0 12 12"><path d="M5 7 7 5M4.5 5.5 3 7a1.8 1.8 0 0 0 2 2l1.5-1.5M7.5 6.5 9 5a1.8 1.8 0 0 0-2-2L5.5 4.5" fill="none" stroke="#2b5f94" stroke-width="1.4" stroke-linecap="round"/></svg>www.DrDovanclinic.example</li>
    </ul>
  </div>
</section>

<section class="card card--back" aria-label="Appointment card back">
  <h2 class="appointment__heading">APPOINTMENT</h2>
  <div class="appointment__fields">
    <div class="field-row"><span class="label">For :</span><span class="line"></span><span class="label">Time :</span><span class="line"></span></div>
    <div class="field-row"><span class="label">Date :</span><span class="line"></span></div>
    <div class="field-row"><span class="label">Location :</span><span class="line"></span></div>
  </div>
  <hr class="appointment__divider">
  <p class="appointment__note">If you are unable to keep appointment, please contact<br>us as soon as possible. Call 877 555 0142<br>www.DrDovanclinic.example</p>
</section>

</body>
</html>
```